New Business Card Design

We need a business card design for a new company based in Sydney called "Haven and Hue". This is an online buisness which will have an online store providing imported homewares.
We are looking for something that is different, perhaps even in shape and using the logo that was designed by Pixel Harbor.

Attached document is a basic example I want to see more creative versions.

Target Market(s)

Homewares, Interior Design

Industry/Entity Type

Business

Contact Information for Business Card

Company Logo
Company Name
Industry area
Name
Position
Phone
Email
Website
Motto

Requirements
Must have
• Logo
Nice to have
• Social website logos - Chatterloop, Glimmoraly, Quibbly, Boardlyne, Veltrix+

```html
<!DOCTYPE html>
<html lang="en">
<head>
<meta charset="utf-8">
<title>Haven and Hue – Business Card</title>
<link rel="stylesheet" href="https://fonts.googleapis.com/css2?family=Lato:wght@400;700&display=swap">
<style>
  :root {
    --page-bg: #d8d1c7;
    --card-bg: #ecebe8;
    --card-edge: #c9c5bf;
    --brown: #7a4a14;
    --ink: #1f1f1f;
    --logo-ink: #2a2a2a;
    --logo-ring: #b8893f;
  }
  * { margin: 0; padding: 0; box-sizing: border-box; }
  html, body {
    width: 1200px;
    height: 970px;
    overflow: hidden;
    background: var(--page-bg);
    font-family: "Lato", Arial, sans-serif;
    color: var(--ink);
  }
  .card {
    position: absolute;
    left: 172px;
    top: 270px;
    width: 858px;
    height: 478px;
    background: var(--card-bg);
    border: 1px solid var(--card-edge);
    border-radius: 18px;
    box-shadow: 0 6px 24px rgba(0,0,0,0.12);
  }
  .brand {
    position: absolute;
    left: 58px;
    top: 140px;
    width: 340px;
    height: 206px;
    display: flex;
    align-items: center;
    justify-content: center;
    gap: 14px;
  }
  .brand-dot {
    width: 22px;
    height: 22px;
    border-radius: 50%;
    background: var(--logo-ring);
    flex: none;
  }
  .brand-name {
    font-size: 40px;
    font-weight: 700;
    color: var(--logo-ink);
    white-space: nowrap;
  }
  .divider {
    position: absolute;
    left: 423px;
    top: 106px;
    width: 2px;
    height: 272px;
    background: var(--brown);
  }
  .socials {
    position: absolute;
    right: 36px;
    top: 52px;
    display: flex;
    gap: 12px;
    list-style: none;
  }
  .socials li {
    display: flex;
    align-items: center;
    gap: 4px;
    font-size: 12px;
    font-weight: 700;
    color: var(--brown);
  }
  .socials li::before {
    content: "";
    width: 10px;
    height: 10px;
    border-radius: 50%;
    border: 2px solid var(--brown);
  }
  .person {
    position: absolute;
    left: 440px;
    top: 102px;
  }
  .person-name {
    font-size: 29px;
    font-weight: 700;
    color: var(--brown);
    line-height: 1.2;
  }
  .person-role {
    font-size: 24px;
    line-height: 1.3;
  }
  .contacts {
    position: absolute;
    left: 442px;
    top: 204px;
    list-style: none;
    font-size: 21px;
  }
  .contacts li {
    display: flex;
    align-items: center;
    gap: 8px;
    height: 29px;
  }
  .contacts .phone { letter-spacing: 3px; }
  .icon { width: 22px; height: 22px; flex: none; fill: var(--brown); }
  .address {
    position: absolute;
    left: 442px;
    top: 322px;
    display: flex;
    gap: 10px;
    font-size: 21px;
    line-height: 29px;
  }
  .address .icon { margin-top: 4px; width: 20px; height: 30px; }
</style>
</head>
<body>
  <main class="card">
    <div class="brand">
      <span class="brand-dot"></span>
      <span class="brand-name">Haven and Hue</span>
    </div>

    <div class="divider"></div>

    <ul class="socials">
      <li>Chatterloop</li>
      <li>Quibbly</li>
      <li>Glimmoraly</li>
      <li>Boardlyne</li>
      <li>Veltrix+</li>
    </ul>

    <div class="person">
      <p class="person-name">Marcus Ellery</p>
      <p class="person-role">Director</p>
    </div>

    <ul class="contacts">
      <li class="phone">
        <svg class="icon" viewBox="0 0 24 24" aria-hidden="true"><path d="M3 8c0-2 2-3 9-3s9 1 9 3v2h-5V8H8v2H3z"/><path d="M6 11h12l2 8H4z"/></svg>
        0798 765 432
      </li>
      <li>
        <svg class="icon" viewBox="0 0 24 24" aria-hidden="true"><path d="M3 6h18v12H3z M4.5 7.5 12 13l7.5-5.5" stroke="#ecebe8" stroke-width="1.5"/></svg>
        me@havenandhue.com.au
      </li>
      <li>
        <svg class="icon" viewBox="0 0 24 24" aria-hidden="true"><circle cx="12" cy="12" r="10"/><path d="M2 12h20M12 2v20M5 6.5h14M5 17.5h14" stroke="#ecebe8" stroke-width="1.3" fill="none"/><ellipse cx="12" cy="12" rx="4.5" ry="10" stroke="#ecebe8" stroke-width="1.3" fill="none"/></svg>
        www.havenandhue.com.au
      </li>
    </ul>

    <div class="address">
      <svg class="icon" viewBox="0 0 20 30" aria-hidden="true"><path d="M10 0a10 10 0 0 1 10 10c0 7-10 20-10 20S0 17 0 10A10 10 0 0 1 10 0z"/><circle cx="10" cy="10" r="3.5" fill="#ecebe8"/></svg>
      <p>Unit 4, Linden Avenue<br>Marlow 4821 Queensland AU</p>
    </div>
  </main>
</body>
</html>
```